Online interactive tutorial for year 2 to year 12 students in Australia

Website design for a new online tutorial for year 2 to year 12 students in Australia.

- The tutorial will be conducted via live webcam and within a dedicated interactive space
- The tutorial will be provided by high scoring undergraduates studying in top Australian universities.
- The tutors will be going through interviews & assessments & only top students are allowed to apply.
- Parents will do search and select tutor and have short 15 mins video interaction with potential tutors before booking them for their children for tutoring.
- hourly cost of booking (no monthly subscription or no hour limits)
- Tutors will have their own profile

Please see the attached for detailed page functionality.

The look and feel of the design must consider the following:
- must be educational but not dull and should stand out
- must appeal to younger generation - tutees (8-18 years), tutors (19-25), parents (30-50).
- Ideas for Logos (brivora.com.au but not confirmed)

Target Market(s)

tutees (8-18 years), tutors (19-25 years), parents (30-50 years).

Industry/Entity Type

Education

Coding

Coded - Design and coding required

Number of Pages Required

5+ page

Font styles to use
Serif

Requirements
Must have
• The look and feel of the design must consider the following:
• - must be educational but not dull and should stand out
• - must appeal to younger generation - tutees (8-18 years), tutors (19-25), parents (30-50).
Should not have
• Dullness

```html
<!DOCTYPE html>
<html lang="en">
<head>
<meta charset="utf-8">
<title>Brivora – Learning Space</title>
<link href="https://fonts.googleapis.com/css2?family=Roboto:wght@400;500;700&family=Roboto+Condensed:wght@700&family=Open+Sans:wght@400;600&display=swap" rel="stylesheet">
<style>
:root{
  --blue:#2a7fc5;
  --sky:#1a9ad6;
  --navy:#1f5f9e;
  --red:#d8292b;
  --ink:#333;
  --muted:#555;
  --line:#dcdcdc;
  --footer:#333333;
  --yellow:#f7be3b;
  --teal:#2ccbb5;
  --coral:#f2555a;
  --green:#4ab625;
  --aqua:#20c4c0;
  --azure:#2196d8;
  --crimson:#e3262c;
}
*{margin:0;padding:0;box-sizing:border-box}
html,body{width:957px;height:1200px;overflow:hidden;background:#fff;font-family:"Open Sans",sans-serif;color:var(--ink)}
.page{position:relative;width:957px;height:1200px}
.abs{position:absolute}

/* header */
.brand{left:78px;top:20px;display:flex;align-items:center;gap:8px}
.brand-mark{width:30px;height:30px;border-radius:50%;background:var(--blue)}
.brand-name{font:700 30px "Roboto",sans-serif;color:#4a4a4a}
.search{left:289px;top:30px;width:288px;height:27px;border:1px solid #cfcfcf;border-radius:2px;display:flex;font-size:9px;color:#555}
.search span{flex:1;padding:7px 11px}
.search .caret{width:24px;display:flex;align-items:center;justify-content:center;flex:none;padding:0}
.search .go{width:31px;background:#e9e9e9;border-left:1px solid #cfcfcf;display:flex;align-items:center;justify-content:center;flex:none;padding:0}
.role{top:31px;height:26px;border:2px solid var(--navy);border-radius:2px;color:var(--navy);font:500 11px "Roboto",sans-serif;display:flex;align-items:center;justify-content:center;gap:5px}
.login{left:823px;top:31px;width:55px;height:26px;background:var(--blue);color:#fff;border-radius:2px;font:500 11px "Roboto",sans-serif;display:flex;align-items:center;justify-content:center}

/* nav */
.nav{left:0;top:92px;width:957px;height:39px;background:var(--blue)}
.nav a{position:absolute;top:0;height:39px;line-height:39px;color:#fff;font:500 11px/39px "Roboto",sans-serif;text-decoration:none;transform:translateX(-50%);white-space:nowrap}
.nav i{position:absolute;top:0;width:1px;height:39px;background:#2470b0}

/* hero */
.hero{left:0;top:131px;width:957px;height:262px}
.hero-title{left:0;top:252px;width:957px;text-align:center;font:700 33px "Roboto Condensed",sans-serif;color:#fff;text-shadow:0 2px 4px rgba(0,0,0,.35)}

/* tools */
.tool{top:462px;width:110px;text-align:center;transform:translateX(-50%)}
.tool .disc{width:67px;height:67px;border-radius:50%;margin:0 auto 8px;display:flex;align-items:center;justify-content:center}
.tool p{font:400 13px "Roboto",sans-serif;color:#444;white-space:nowrap}

/* workspace */
.workspace{left:114px;top:594px;width:730px;height:245px;background:#fafafa;border:1px solid var(--line);box-shadow:inset 0 0 12px rgba(0,0,0,.05)}
.tab{top:604px;text-align:center;transform:translateX(-50%);font:400 12px "Roboto",sans-serif;color:#555}
.tab svg{display:block;margin:0 auto 6px}
.tab-sep{top:594px;width:1px;height:60px;background:#e8e8e8}
.timer{left:652px;top:614px;font-size:10px;color:#555}
.timer b{font-weight:400;margin-left:8px}
.editor{left:134px;top:654px;width:691px;height:164px;background:#fff;border:1px solid #e4e4e4}
.editor p{padding:27px 15px;font-size:10px;color:#444}
.notch{left:172px;top:646px;width:14px;height:14px;background:#fff;border-left:1px solid #e4e4e4;border-top:1px solid #e4e4e4;transform:rotate(45deg)}
.btn{top:862px;width:79px;height:26px;color:#fff;border-radius:2px;font:500 13px "Roboto",sans-serif;display:flex;align-items:center;justify-content:center}

/* footer */
.footer{left:0;top:928px;width:957px;height:232px;background:var(--footer);color:#fff}
.footer h3{position:absolute;font:400 15px "Roboto",sans-serif}
.footer p,.footer li{font-size:11px;line-height:16px}
.links{list-style:none;position:absolute;left:340px;top:67px}
.links li{height:17px;padding-left:14px;position:relative}
.links li::before{content:"";position:absolute;left:0;top:5px;border-left:4px solid #fff;border-top:3px solid transparent;border-bottom:3px solid transparent}
.field{position:absolute;left:497px;top:100px;width:234px;height:33px;background:#fff;color:#555;font-size:9px;padding:11px 11px}
.subscribe{position:absolute;left:497px;top:140px;width:82px;height:33px;background:var(--sky);font:500 11px/33px "Roboto",sans-serif;text-align:center}
.social{position:absolute;left:802px;top:64px;list-style:none}
.social li{display:flex;align-items:center;gap:8px;height:29px;font-size:12px}
.social li::before{content:"";width:19px;height:19px;border:1px solid #aaa;border-radius:50%}
.bottom{left:0;top:1160px;width:957px;height:40px;background:var(--sky);color:#fff;font-size:10px;text-align:center;line-height:40px}
</style>
</head>
<body>
<div class="page">

  <!-- header -->
  <div class="abs brand"><span class="brand-mark"></span><span class="brand-name">Brivora</span></div>
  <div class="abs search">
    <span>Search</span>
    <span class="caret"><svg width="7" height="4"><path d="M0 0h7L3.5 4z" fill="#777"/></svg></span>
    <span class="go"><svg width="11" height="11" viewBox="0 0 11 11"><circle cx="4.5" cy="4.5" r="3.3" fill="none" stroke="#444" stroke-width="1.6"/><path d="M7 7l3 3" stroke="#444" stroke-width="1.8"/></svg></span>
  </div>
  <div class="abs role" style="left:594px;width:62px"><svg width="9" height="10"><circle cx="4.5" cy="2.8" r="2.6" fill="#1f5f9e"/><path d="M0 10c0-4 9-4 9 0z" fill="#1f5f9e"/></svg>Tutor</div>
  <div class="abs role" style="left:664px;width:66px"><svg width="11" height="10"><circle cx="3" cy="2" r="1.8" fill="#1f5f9e"/><circle cx="8" cy="2" r="1.8" fill="#1f5f9e"/><rect x="1" y="4.5" width="4" height="5.5" fill="#1f5f9e"/><rect x="6" y="4.5" width="4" height="5.5" fill="#1f5f9e"/></svg>Parent</div>
  <div class="abs role" style="left:740px;width:74px"><svg width="11" height="10"><path d="M0 2l5.5-2 5.5 2-5.5 2z" fill="#1f5f9e"/><path d="M3 4.5h5v2.5H3zM1.5 10c0-3 8-3 8 0z" fill="#1f5f9e"/></svg>Tutees</div>
  <div class="abs login">LOGIN</div>

  <!-- navigation -->
  <nav class="abs nav">
    <a style="left:112px">HOME</a><i style="left:150px"></i>
    <a style="left:215px">TUTOR PROFILES</a><i style="left:280px"></i>
    <a style="left:335px">HOW IT WORKS</a><i style="left:395px"></i>
    <a style="left:451px">TESTIMONIALS</a><i style="left:511px"></i>
    <a style="left:547px">PRICES</a><i style="left:586px"></i>
    <a style="left:636px">CONTACT US</a>
  </nav>

  <!-- hero -->
  <svg class="abs hero" viewBox="0 0 957 262" role="img" aria-label="Desk photo with keyboard, notebook, pencil, mouse and a green plant">
    <defs>
      <linearGradient id="desk" x1="0" y1="0" x2="1" y2="0">
        <stop offset="0" stop-color="#9b9a94"/>
        <stop offset="0.5" stop-color="#7b6d5c"/>
        <stop offset="1" stop-color="#5a5a3e"/>
      </linearGradient>
    </defs>
    <path d="M0 0h957v205L478 258 0 205z" fill="url(#desk)"/>
    <path d="M0 205L478 258 957 205" fill="none" stroke="#1a9ad6" stroke-width="4"/>
  </svg>
  <div class="abs hero-title">LEARNING SPACE</div>
  <svg class="abs" style="left:449px;top:365px" width="58" height="58" viewBox="0 0 58 58">
    <circle cx="29" cy="29" r="29" fill="#1a9ad6"/>
    <path d="M0 29a29 29 0 0 0 58 0z" fill="#1780b8"/>
    <circle cx="29" cy="26" r="14" fill="#f2f2f2"/>
    <circle cx="29" cy="26" r="8" fill="#2d3e4c"/>
    <circle cx="29" cy="26" r="3.5" fill="#0e1a22"/>
    <path d="M20 45c2-5 16-5 18 0z" fill="#f2f2f2"/>
  </svg>

  <!-- tools -->
  <div class="abs tool" style="left:155px"><div class="disc" style="background:var(--yellow)"><svg width="32" height="30"><rect x="3" y="5" width="20" height="22" fill="none" stroke="#fff" stroke-width="2.5"/><path d="M7 11h10M7 16h10M7 21h7" stroke="#fff" stroke-width="2"/><path d="M19 22l9-12 2 2-9 12z" fill="#fff"/></svg></div><p>Writing Pad</p></div>
  <div class="abs tool" style="left:260px"><div class="disc" style="background:var(--teal)"><svg width="32" height="30"><rect x="3" y="8" width="24" height="18" fill="none" stroke="#fff" stroke-width="2.5"/><path d="M12 19l12-14 3 3-12 14-4 1z" fill="#fff"/></svg></div><p>Drawing Pad</p></div>
  <div class="abs tool" style="left:365px"><div class="disc" style="background:var(--coral)"><svg width="28" height="28"><path d="M3 3h18l5 5v17H3z" fill="none" stroke="#fff" stroke-width="2.5"/><rect x="8" y="4" width="11" height="7" fill="#fff"/><rect x="8" y="16" width="13" height="8" fill="none" stroke="#fff" stroke-width="2"/></svg></div><p>Save Work</p></div>
  <div class="abs tool" style="left:470px"><div class="disc" style="background:var(--green)"><svg width="32" height="30"><path d="M16 2l9 9h-5v8h-8v-8H7z" fill="#fff"/><rect x="3" y="20" width="26" height="8" fill="#fff"/></svg></div><p>Upload Work</p></div>
  <div class="abs tool" style="left:581px"><div class="disc" style="background:var(--aqua)"><svg width="26" height="32"><path d="M2 2h15l7 7v21H2z" fill="none" stroke="#fff" stroke-width="2.5"/><path d="M7 14h12M7 19h12M7 24h12" stroke="#fff" stroke-width="2"/></svg></div><p>Access to Docs</p></div>
  <div class="abs tool" style="left:686px"><div class="disc" style="background:var(--azure)"><svg width="30" height="30"><rect x="3" y="4" width="24" height="22" fill="none" stroke="#fff" stroke-width="2.5"/><path d="M3 11h24M3 18h24M13 4v22" stroke="#fff" stroke-width="2"/></svg></div><p>Spreadsheet</p></div>
  <div class="abs tool" style="left:792px"><div class="disc" style="background:var(--crimson)"><svg width="26" height="32"><path d="M2 2h15l7 7v21H2z" fill="none" stroke="#fff" stroke-width="2.5"/><rect x="6" y="13" width="14" height="10" fill="#fff"/></svg></div><p>Pdf Application</p></div>

  <!-- workspace -->
  <div class="abs workspace"></div>
  <div class="abs tab-sep" style="left:243px"></div>
  <div class="abs tab-sep" style="left:316px"></div>
  <div class="abs tab-sep" style="left:390px"></div>
  <div class="abs tab" style="left:178px"><svg width="14" height="14"><path d="M2 12l1-4 8-7 3 3-8 7z" fill="#555"/></svg>Post Comments</div>
  <div class="abs tab" style="left:277px"><svg width="14" height="14"><circle cx="11" cy="3" r="2.3" fill="#555"/><circle cx="3" cy="7" r="2.3" fill="#555"/><circle cx="11" cy="11" r="2.3" fill="#555"/><path d="M11 3L3 7l8 4" stroke="#555" stroke-width="1.3" fill="none"/></svg>Share</div>
  <div class="abs tab" style="left:354px"><svg width="14" height="14"><path d="M7 0l5 5H9v4H5V5H2z" fill="#555"/><rect x="1" y="10" width="12" height="4" fill="#555"/></svg>Upload</div>
  <div class="abs tab" style="left:424px"><svg width="16" height="14"><path d="M1 2h5l1 2h6v2H4L1 12z" fill="#555"/><path d="M4 7h12l-3 6H1z" fill="#555"/></svg>Open</div>
  <div class="abs tab" style="left:487px"><svg width="14" height="14"><path d="M1 1h10l2 2v10H1z" fill="none" stroke="#555" stroke-width="1.4"/><rect x="4" y="2" width="5" height="4" fill="#555"/></svg>saved</div>
  <div class="abs timer">Session Time Remaining :<b>56m</b><b>45s</b></div>
  <div class="abs editor"><p>Sed ut perspiciatis unde omnis iste natus|</p></div>
  <div class="abs notch"></div>
  <div class="abs btn" style="left:395px;background:var(--red)">Recorded</div>
  <div class="abs btn" style="left:484px;background:#2a73b9">Saved</div>

  <!-- footer -->
  <footer class="abs footer">
    <h3 style="left:78px;top:29px">CONTACT US</h3>
    <p style="position:absolute;left:78px;top:60px">Level 3, 28 Harbour Lane, Brisbane<br>QLD 4000, Australia</p>
    <svg style="position:absolute;left:80px;top:105px" width="15" height="15"><path d="M3 1l3 3-2 2c1 2 3 4 5 5l2-2 3 3-2 2C7 14 1 8 1 3z" fill="none" stroke="#ddd" stroke-width="1.1"/></svg>
    <p style="position:absolute;left:108px;top:102px">Phone : +61 7 3000 1482<br>Fax : +61 7 3000 1483</p>
    <svg style="position:absolute;left:80px;top:147px" width="15" height="11"><rect x="0.5" y="0.5" width="14" height="10" fill="none" stroke="#ddd"/><path d="M0.5 0.5l7 6 7-6" fill="none" stroke="#ddd"/></svg>
    <p style="position:absolute;left:108px;top:144px">Email: info@brivora.com.au</p>

    <h3 style="left:338px;top:29px">USEFUL LINKS</h3>
    <ul class="links">
      <li>Home</li><li>About Us</li><li>Services</li><li>Tutor Profile</li><li>How It Works</li><li>Scheduler</li><li>Testimonials</li><li>Contact Us</li>
    </ul>

    <h3 style="left:497px;top:29px">JOIN OUR NEWSLETTER</h3>
    <p style="position:absolute;left:497px;top:58px;width:240px;font-size:9px;line-height:15px">Sed ut perspiciatis unde omnis iste natus error sit volup-tatem accusantium doloremque laudantium,</p>
    <div class="field">Enter Name</div>
    <div class="subscribe">SUBSCRIBE</div>

    <h3 style="left:802px;top:29px">SOCIAL</h3>
    <ul class="social">
      <li>Pagewall</li><li>Chirpline</li><li>Circlenet</li><li>Vidstream</li>
    </ul>
  </footer>
  <div class="abs bottom">Copyright 2016 | All Rights Reserved -- Brivora</div>
</div>
</body>
</html>
```